Road Construction Company needs business cards

We would like a new business card designed for our business.

We're a road construction company based in Qld, Australia.

Can the business card please have the following information on it.

Name: Warren Halbeck
Position: General Manager
Phone: 0472 915 348
Email: Warren.halbeck@tovrin.com.au
Address: 87 Marrow Ave, Pendlebay, QLD, 4023
Website: www.tovrin.com.au

Visually we'd like the card to be professional and simple.

Attached is our logo.

Our website is www.tovrin.com.au

Target Market(s)

Men aged 25-60

Contact Information for Business Card

As listed in project description

Font styles to use
Serif

Requirements
Must have
• Large logo on back of card

```html
<!DOCTYPE html>
<html lang="en">
<head>
<meta charset="utf-8">
<title>Tovrin Business Card</title>
<link rel="stylesheet" href="https://fonts.googleapis.com/css2?family=Arimo:wght@400;700&display=swap">
<style>
  :root {
    --backdrop: #646464;
    --brand-blue: #0c56a2;
    --card-white: #ffffff;
    --ink-white: #ffffff;
  }
  html, body {
    margin: 0;
    padding: 0;
    width: 1200px;
    height: 2250px;
    overflow: hidden;
    background: var(--backdrop);
  }
  .canvas {
    position: relative;
    width: 1200px;
    height: 2250px;
    font-family: "Arimo", Arial, sans-serif;
  }
  .card {
    position: absolute;
    box-sizing: border-box;
  }
  .card-back {
    left: 120px;
    top: 78px;
    width: 990px;
    height: 564px;
    background: var(--brand-blue);
    display: flex;
    align-items: center;
    justify-content: center;
  }
  .wordmark {
    margin: 0 0 40px 0;
    color: var(--ink-white);
    font-weight: 700;
    font-size: 76px;
    letter-spacing: 4px;
    line-height: 1;
  }
  .card-front {
    left: 123px;
    top: 676px;
    width: 992px;
    height: 565px;
    background: var(--card-white);
    color: var(--brand-blue);
  }
  .person {
    position: absolute;
    right: 119px;
    top: 118px;
    text-align: center;
  }
  .person-name {
    margin: 0;
    font-weight: 700;
    font-size: 27px;
    letter-spacing: 0.5px;
    line-height: 1.1;
  }
  .person-role {
    margin: 2px 0 0;
    font-weight: 700;
    font-size: 14px;
    letter-spacing: 1px;
  }
  .contact-list {
    position: absolute;
    left: 0;
    top: 0;
    margin: 0;
    padding: 0;
    list-style: none;
  }
  .contact-item {
    position: absolute;
    display: flex;
    align-items: center;
    gap: 14px;
    white-space: nowrap;
    font-weight: 700;
    font-size: 17px;
    letter-spacing: 1.2px;
  }
  .contact-item svg {
    width: 28px;
    height: 28px;
    flex: none;
  }
  .email   { left: 99px;  top: 331px; }
  .phone   { left: 99px;  top: 374px; }
  .address { left: 486px; top: 331px; }
  .website { left: 486px; top: 374px; }
</style>
</head>
<body>
<main class="canvas">
  <section class="card card-back" aria-label="Card back">
    <h1 class="wordmark">TOVRIN</h1>
  </section>

  <section class="card card-front" aria-label="Card front">
    <div class="person">
      <h2 class="person-name">WARREN HALBECK</h2>
      <p class="person-role">GENERAL MANAGER</p>
    </div>
    <ul class="contact-list">
      <li class="contact-item email">
        <svg viewBox="0 0 28 28" aria-hidden="true"><circle cx="14" cy="14" r="14" fill="#0c56a2"/><rect x="7.5" y="9.5" width="13" height="9" rx="1" fill="none" stroke="#fff" stroke-width="1.6"/><path d="M8 10.5 L14 15 L20 10.5" fill="none" stroke="#fff" stroke-width="1.6"/></svg>
        <span>Warren.halbeck@tovrin.com.au</span>
      </li>
      <li class="contact-item phone">
        <svg viewBox="0 0 28 28" aria-hidden="true"><circle cx="14" cy="14" r="14" fill="#0c56a2"/><path d="M10 7.5c.8-.5 1.5 0 1.9.7l1.2 2.3c.3.6.1 1.2-.4 1.6l-.9.7c.6 1.6 1.8 2.9 3.4 3.6l.8-.9c.4-.5 1.1-.6 1.6-.3l2.3 1.3c.7.4 1 1.2.5 1.9l-.9 1.1c-.6.7-1.6 1-2.5.7-4.2-1.4-7.2-4.5-8.5-8.6-.3-.9 0-1.9.7-2.5z" fill="#fff"/></svg>
        <span>0472 915 348</span>
      </li>
      <li class="contact-item address">
        <svg viewBox="0 0 28 28" aria-hidden="true"><circle cx="14" cy="14" r="14" fill="#0c56a2"/><path d="M14 7 L21.5 13.5 H19.5 V20.5 H15.7 V16.5 H12.3 V20.5 H8.5 V13.5 H6.5 Z" fill="#fff"/></svg>
        <span>87 Marrow Ave, Pendlebay, QLD, 4023</span>
      </li>
      <li class="contact-item website">
        <svg viewBox="0 0 28 28" aria-hidden="true"><circle cx="14" cy="14" r="14" fill="#0c56a2"/><circle cx="14" cy="14" r="7" fill="none" stroke="#fff" stroke-width="1.6"/><ellipse cx="14" cy="14" rx="3" ry="7" fill="none" stroke="#fff" stroke-width="1.4"/><path d="M7 14 H21" stroke="#fff" stroke-width="1.4"/></svg>
        <span>www.tovrin.com.au</span>
      </li>
    </ul>
  </section>
</main>
</body>
</html>
```